Luxury Wine Label for New Startup Winery

We need a wine label for our new winery startup. We have worked with a local designer but do not feel the resulting label / logo have the elevation required to present our brand as a luxury wine. Our winery is called "Quailbrook Vineyards" and we are focused on extremely high quality hand crafted artisan and estate wines from the Pacific Northwest.
We would like to see designs that utilize a tree line, or other imagery that represents the "Quailbrook" part of our company name. Another interesting feature could be wood grain.
A logo will be required based on your design so please design with this in mind:
This logo should be consistent with the wine bottle label design, and should be representative of our high end exclusive wine while giving a sense of place (Oregon/ Pacific Northwest.)
I will supply an image of the design we received from our local designer, PLEASE NOTE: in general we do like wood grain and tree line concepts but feel the execution was poorly done.
ATTN: Logo design should be suitable for use on: Bottles (Red wine/rose/white wine), Bussiness cards, vehicle signage, business signage, etc
P.S.:
If you have a design that is not outside the box we are still interested in seeing it.
Label is for a burgundy style bottle with a label height of 3.5 - 4" and a width of 3.5-4"
any label <= 4"x4" and >=3.5"x3.5" will be acceptable:
HOWEVER Width should be greater than or equal to height due to the bottle format
Target Market(s)
Wine enthusiasts with adequate discretionary budgets to afford $100 bottles of wine.
Industry/Entity Type
Wine / Winery
Requirements
Must have
- A sense of luxury, a feel of exclusivity, and a theme consistent with our product and brand name
Nice to have
- Tree line, wood grain or other wood themes. Serif fonts
Should not have
- anything cheesy, off topic, hard to read script fonts or anything that makes the label hard to read from a few feet away or too busy

```html
<!DOCTYPE html>
<html lang="en">
<head>
<meta charset="UTF-8">
<title>Quailbrook Vineyards – Wine Label</title>
<link href="https://fonts.googleapis.com/css2?family=Josefin+Sans:wght@300;400&family=Pinyon+Script&display=swap" rel="stylesheet">
<style>
  :root {
    --ground: #1e1513;
    --gold: #c9a24a;
    --gold-light: #e8cf84;
    --gold-deep: #9a7428;
    --wood-dark: #2a150d;
    --wood-mid: #5a3020;
    --wood-light: #7b4a30;
    --ink: #f4efe6;
    --ink-soft: #d9d2c6;
  }
  * { margin: 0; padding: 0; box-sizing: border-box; }
  html, body { width: 1200px; height: 999px; overflow: hidden; }
  body {
    background: var(--ground);
    font-family: "Josefin Sans", sans-serif;
    font-weight: 300;
    color: var(--ink);
  }
  .label { position: relative; width: 1200px; height: 999px; }

  .emblem { position: absolute; left: 308px; top: 40px; width: 584px; height: 584px; }
  .emblem svg { display: block; width: 100%; height: 100%; }
  .emblem .wood { position: absolute; left: 0; top: 0; }

  .emblem-text {
    position: absolute; left: 0; top: 0; width: 100%; height: 100%;
    text-align: center;
  }
  .brand-name {
    position: absolute; left: 60px; right: 60px; top: 214px;
    font-weight: 300; font-size: 60px; line-height: 66px;
    color: var(--gold); letter-spacing: 0; text-transform: uppercase;
    white-space: nowrap;
  }
  .tagline {
    position: absolute; left: 0; right: 0; top: 384px;
    font-size: 19px; line-height: 29px; letter-spacing: 2px;
    color: var(--ink-soft); text-transform: uppercase;
  }

  .details { position: absolute; left: 0; top: 0; width: 1200px; height: 999px; }
  .hand-crafted {
    position: absolute; left: 0; right: 0; top: 640px;
    text-align: center; font-size: 40px; text-transform: uppercase;
  }
  .col { position: absolute; top: 702px; text-transform: uppercase; }
  .col-left { left: 346px; width: 230px; }
  .col-right { left: 626px; width: 240px; }
  .col-title { font-size: 28px; line-height: 36px; white-space: nowrap; }
  .col-sub { font-size: 20px; line-height: 28px; margin-top: 24px; white-space: nowrap; }
  .field {
    height: 46px; border: 2px solid var(--ink-soft); margin-top: 6px;
  }
  .col-left .field { width: 220px; }
  .col-right .field { width: 236px; text-align: center; }
  .signature {
    font-family: "Pinyon Script", cursive; text-transform: none;
    font-size: 34px; line-height: 42px; color: var(--ink);
  }
  .divider {
    position: absolute; left: 600px; top: 706px; width: 2px; height: 140px;
    background: var(--ink-soft);
  }
  .footer-line {
    position: absolute; left: 0; right: 0; top: 922px;
    display: flex; justify-content: center; align-items: baseline; gap: 34px;
    text-transform: uppercase; color: var(--ink-soft);
  }
  .footer-line .small { font-size: 21px; letter-spacing: 1px; }
  .footer-line .volume { font-size: 40px; color: var(--ink); }
</style>
</head>
<body>
  <main class="label">
    <div class="emblem">
      <svg viewBox="0 0 584 584" aria-hidden="true">
        <defs>
          <linearGradient id="goldRing" x1="0" y1="0" x2="1" y2="1">
            <stop offset="0" stop-color="#e8cf84"/>
            <stop offset="0.45" stop-color="#c9a24a"/>
            <stop offset="1" stop-color="#9a7428"/>
          </linearGradient>
          <radialGradient id="woodFill" cx="0.45" cy="0.45" r="0.6">
            <stop offset="0" stop-color="#7b4a30"/>
            <stop offset="0.55" stop-color="#5a3020"/>
            <stop offset="1" stop-color="#2a150d"/>
          </radialGradient>
        </defs>
        <circle cx="292" cy="292" r="292" fill="url(#goldRing)"/>
      </svg>
      <svg class="wood" viewBox="0 0 584 584" role="img" aria-label="Swirling dark wood grain illustration">
        <circle cx="292" cy="292" r="258" fill="url(#woodFill)"/>
      </svg>
      <div class="emblem-text">
        <p class="brand-name">Quailbrook<br>Vineyards</p>
        <p class="tagline">A rebellious spirit with<br>Pacific Northwest<br>caracter</p>
      </div>
    </div>

    <section class="details">
      <p class="hand-crafted">Hand Crafted</p>
      <div class="col col-left">
        <p class="col-title">Single Barrel</p>
        <p class="col-sub">Barrel Number</p>
        <div class="field"></div>
      </div>
      <div class="divider"></div>
      <div class="col col-right">
        <p class="col-title">Cask Strength</p>
        <p class="col-sub">Master Distiller</p>
        <div class="field"><span class="signature">Evan Hale</span></div>
      </div>
      <p class="footer-line">
        <span class="small">Product of Oregon</span>
        <span class="volume">750 ML</span>
        <span class="small">40% Alc./Vol</span>
      </p>
    </section>
  </main>
</body>
</html>
```